Business Card for a New Zealand IT Startup

I need a business card for VELTA Holdings. We are a young startup based in New Zealand working in internet marketing and web development. The design should have some element connected to New Zealand, such as wave, koru or silver fern, just don't use a kiwi bird.

```html
<!DOCTYPE html>
<html lang="en">
<head>
<meta charset="utf-8">
<title>VELTA Holdings – Business Card</title>
<link rel="stylesheet" href="https://fonts.googleapis.com/css2?family=Montserrat:wght@600&family=Open+Sans:wght@400;600&display=swap">
<style>
  :root {
    --backdrop: #dcd8d3;
    --card: #eef0f1;
    --card-edge: #ffffff;
    --brand-blue: #1e6fa6;
    --brand-orange: #cf5f2c;
    --ink: #2b2b2b;
    --ink-soft: #444444;
  }
  html, body {
    margin: 0;
    padding: 0;
    width: 1200px;
    height: 1054px;
    overflow: hidden;
    background: var(--backdrop);
  }
  .business-card {
    position: absolute;
    left: 100px;
    top: 224px;
    width: 1000px;
    height: 605px;
    background: var(--card);
    border: 1px solid var(--card-edge);
    box-shadow: 0 10px 30px rgba(0,0,0,0.12);
    font-family: "Open Sans", Arial, sans-serif;
  }
  .brand-name {
    position: absolute;
    left: 0;
    right: 0;
    top: 148px;
    margin: 0;
    text-align: center;
    font-family: "Montserrat", Arial, sans-serif;
    font-weight: 600;
    font-size: 64px;
    line-height: 80px;
    letter-spacing: 6px;
    color: var(--brand-blue);
  }
  .person {
    position: absolute;
    right: 550px;
    top: 418px;
    text-align: right;
    white-space: nowrap;
  }
  .person-name {
    margin: 0;
    font-weight: 600;
    font-size: 37px;
    line-height: 44px;
    color: var(--brand-blue);
  }
  .person-title {
    margin: 0;
    font-size: 22px;
    line-height: 30px;
    color: var(--ink-soft);
  }
  .contact-list {
    position: absolute;
    left: 490px;
    top: 396px;
    margin: 0;
    padding: 0;
    list-style: none;
  }
  .contact-item {
    display: flex;
    align-items: center;
    height: 35px;
    font-size: 24px;
    color: var(--ink);
    white-space: nowrap;
  }
  .contact-icon {
    width: 22px;
    height: 22px;
    margin-right: 30px;
    fill: var(--brand-orange);
  }
  .wave-divider {
    position: absolute;
    left: 45px;
    top: 526px;
    width: 910px;
    height: 28px;
  }
  .address {
    position: absolute;
    left: 0;
    right: 0;
    top: 552px;
    margin: 0;
    text-align: center;
    font-size: 23px;
    color: var(--ink);
  }
</style>
</head>
<body>
  <article class="business-card">
    <h1 class="brand-name">VELTA HOLDINGS</h1>

    <div class="person">
      <p class="person-name">Aria Tane Walker</p>
      <p class="person-title">Managing Director</p>
    </div>

    <ul class="contact-list">
      <li class="contact-item">
        <svg class="contact-icon" viewBox="0 0 24 24" aria-hidden="true">
          <path d="M3 9c0-3 4-5 9-5s9 2 9 5v2h-5V9c-1-1-7-1-8 0v2H3z"/>
          <path d="M6 12h12l2 8H4z"/>
        </svg>
        555-0142-318
      </li>
      <li class="contact-item">
        <svg class="contact-icon" viewBox="0 0 24 24" aria-hidden="true">
          <path d="M2 5h20v14H2z M4 7l8 6 8-6" stroke="#eef0f1" stroke-width="1.5"/>
        </svg>
        hello@veltaholdings.com
      </li>
      <li class="contact-item">
        <svg class="contact-icon" viewBox="0 0 24 24" aria-hidden="true">
          <circle cx="12" cy="12" r="10"/>
          <path d="M2 12h20M12 2c-4 5-4 15 0 20M12 2c4 5 4 15 0 20" fill="none" stroke="#eef0f1" stroke-width="1.3"/>
        </svg>
        www.veltaholdings.com
      </li>
    </ul>

    <svg class="wave-divider" viewBox="0 0 910 28" preserveAspectRatio="none" aria-hidden="true">
      <defs>
        <linearGradient id="wave-stroke" x1="0" y1="0" x2="1" y2="0">
          <stop offset="0" stop-color="#cf5f2c"/>
          <stop offset="1" stop-color="#1e6fa6"/>
        </linearGradient>
      </defs>
      <path d="M0 14 C 76 2, 152 2, 228 14 S 380 26, 455 14 S 607 2, 683 14 S 835 26, 910 14"
            fill="none" stroke="url(#wave-stroke)" stroke-width="2.2"/>
    </svg>

    <p class="address">18 Harbour Lane, Northcote, Auckland, NZ 0627</p>
  </article>
</body>
</html>
```